Valmora Health a direct primary care practice needs a beautiful and customer friendly website

We need a website to showcase our new medical practice. We want to enhance the customer experience and make it easy to navigate to the desired page by placing pillar pages on the home screen. the website needs to be clean and bright.

Target Market(s)

Uninsured, Small businesses that can't afford to offer employees insurance.

Industry/Entity Type

Healthcare

Coding

Coded - Design and coding required

Font styles to use
Serif
Sans Serif

Colors
0592cd
3377b5
0355a3
9bcb3c
acd136

Requirements
Must have
• Must be user friendly, must have pillar pages to help boost SEO ranking, clean and bright, must be close to the in colors to the attached logo.

Content will be very similar to www.quillbrookhealth.example
Nice to have
• Clean and easy to read font

```html
<!DOCTYPE html>
<html lang="en">
<head>
<meta charset="utf-8">
<title>Valmora Health</title>
<link href="https://fonts.googleapis.com/css2?family=Tinos:wght@400;700&family=Arimo:wght@400;700&display=swap" rel="stylesheet">
<style>
:root{
  --navy:#0b3f95;
  --navy-deep:#082f78;
  --blue:#1a75bd;
  --sky:#1c9ad8;
  --green:#8cc63f;
  --green-dark:#7ab82f;
  --ink:#333;
  --muted:#555;
  --light:#f3f3f3;
  --white:#fff;
}
*{margin:0;padding:0;box-sizing:border-box}
html,body{width:1200px;height:4012px;overflow:hidden;background:var(--white)}
body{font-family:"Arimo",Arial,sans-serif;color:var(--ink)}
.page{position:relative;width:1200px;height:4012px;overflow:hidden}
.abs{position:absolute}

/* header */
.brand{position:absolute;font-family:"Tinos",serif;font-size:30px;color:var(--navy);letter-spacing:1px;white-space:nowrap}
.nav{position:absolute;top:62px;left:0;width:1200px;font-family:"Tinos",serif;font-size:15px;color:#333}
.nav a{position:absolute;text-decoration:none;color:inherit;white-space:nowrap}
.nav a.active{color:var(--blue)}

/* hero */
.hero-box{position:absolute;left:210px;top:495px;width:779px;height:237px;background:rgba(26,105,190,.88);text-align:center;color:var(--white)}
.hero-box h1{font-family:"Tinos",serif;font-weight:400;font-size:68px;margin-top:40px;letter-spacing:1px;white-space:nowrap}
.hero-box p{font-family:"Tinos",serif;font-size:19px;line-height:36px;margin-top:8px}

/* section titles */
.section-title{position:absolute;left:0;width:1200px;text-align:center;font-family:"Tinos",serif;font-size:35px;color:var(--navy)}
.rule{position:absolute;left:578px;width:44px;height:2px;background:var(--navy)}

/* services */
.service h3{font-family:"Tinos",serif;font-weight:400;font-size:18px;color:#333;white-space:nowrap}
.service p{font-size:13.5px;line-height:23px;color:var(--muted);margin-top:8px;width:230px}
.service.right-align{text-align:right}
.service.right-align p{margin-left:auto}

/* welcome */
.welcome{position:absolute;left:698px;top:1705px;color:var(--white);width:370px}
.welcome .kicker{font-family:"Tinos",serif;font-size:23px}
.welcome h2{font-family:"Tinos",serif;font-weight:400;font-size:46px;line-height:50px;letter-spacing:.5px;white-space:nowrap}
.welcome p{font-size:14.2px;line-height:25.7px;margin-top:22px;text-align:justify;padding-left:3px}
.pill{position:absolute;left:703px;top:2047px;width:171px;height:64px;border:2px solid var(--white);border-radius:32px;color:var(--white);font-family:"Tinos",serif;font-size:18px;text-align:center;line-height:60px}

/* blog */
.card{position:absolute;width:306px;height:477px;background:var(--white);box-shadow:0 8px 22px rgba(28,120,200,.22)}
.card .thumb{display:block;width:306px;height:207px}
.card h3{font-family:"Tinos",serif;font-weight:400;font-size:17.5px;line-height:27px;color:#222;margin:22px 24px 0}
.card .date{font-family:"Tinos",serif;font-size:17px;color:var(--blue);margin:9px 24px 0;display:flex;align-items:center;gap:6px}
.card p{font-size:13px;line-height:22px;color:var(--muted);margin:13px 24px 0}
.card .btn{display:inline-block;margin:16px 0 0 26px;width:128px;height:44px;border:2px solid var(--blue);border-radius:3px;color:var(--blue);font-family:"Tinos",serif;font-weight:700;font-size:15px;line-height:40px;text-align:center}

/* faq */
.faq-bg{position:absolute;left:0;top:2968px;width:1200px;height:560px;background:var(--light)}
.faq-item{position:absolute;left:195px;width:810px;height:53px;background:var(--white);border-radius:27px;box-shadow:0 3px 10px rgba(0,0,0,.12);font-family:"Tinos",serif;font-size:15.5px;color:#333;line-height:53px;padding-left:23px}
.faq-item svg{position:absolute;right:12px;top:15px}

/* footer */
.foot-text{color:var(--white);font-size:14px;line-height:24px}
.foot-head{font-family:"Tinos",serif;font-size:21px;color:var(--white)}
.contact-row{position:absolute;left:470px;display:flex;gap:16px;color:var(--white);font-size:15px;line-height:23px}
.contact-row svg{flex:none;margin-top:4px}
.email-field{position:absolute;left:763px;top:3686px;width:326px;height:42px;background:var(--white);border:1px solid #ccc;border-radius:2px;font-size:14px;color:#666;line-height:40px;padding-left:19px}
.subscribe{position:absolute;left:763px;top:3745px;width:137px;height:42px;background:var(--green);color:var(--white);font-family:"Tinos",serif;font-weight:700;font-size:15px;text-align:center;line-height:42px}
.bottom-bar{position:absolute;left:0;top:3851px;width:1200px;height:161px;background:var(--navy-deep)}
.social{position:absolute;top:3893px;width:36px;height:36px;border:2px solid var(--white);border-radius:50%}
.copyright{position:absolute;left:0;top:3955px;width:1200px;text-align:center;font-family:"Tinos",serif;font-size:15px;color:var(--white)}
</style>
</head>
<body>
<div class="page">

  <!-- header -->
  <div class="brand" style="left:112px;top:50px;">Valmora Health</div>
  <nav class="nav">
    <a class="active" style="left:470px">HOME</a>
    <a style="left:567px">ABOUT US</a>
    <a style="left:695px">SERVICES</a>
    <a style="left:818px">BLOG</a>
    <a style="left:910px">FAQ</a>
    <a style="left:991px">CONTACT US</a>
  </nav>

  <!-- hero -->
  <svg class="abs" style="left:0;top:137px" width="1200" height="790" viewBox="0 0 1200 790">
    <defs>
      <linearGradient id="heroFill" x1="0" y1="0" x2="1" y2="1">
        <stop offset="0" stop-color="#4a5a6c"/>
        <stop offset=".5" stop-color="#8c9cab"/>
        <stop offset="1" stop-color="#c9d0d6"/>
      </linearGradient>
    </defs>
    <path role="img" aria-label="Photo of a doctor in a white coat consulting with a patient across a desk" d="M0 0H1200V626Q600 876 0 626Z" fill="url(#heroFill)"/>
    <path d="M0 626Q600 900 1200 626V642Q600 918 0 642Z" fill="#0b3f95"/>
  </svg>
  <div class="hero-box">
    <h1>VALMORA HEALTH</h1>
    <p>SED UT PERSPICIATIS UNDE OMNIS ISTE NATUS ERROR SIT VOLUPTATEM<br>ACCUSANTIUM DOLOREMQUE LAUDANTIUM</p>
  </div>

  <!-- services -->
  <div class="section-title" style="top:990px">OUR SERVICES</div>
  <div class="rule" style="top:1048px"></div>

  <svg class="abs" style="left:0;top:1080px" width="1200" height="420" viewBox="0 1080 1200 420">
    <defs>
      <linearGradient id="ring" x1="0" y1="0" x2="1" y2="1">
        <stop offset="0" stop-color="#8cc63f"/>
        <stop offset=".5" stop-color="#1a75bd"/>
        <stop offset="1" stop-color="#8cc63f"/>
      </linearGradient>
    </defs>
    <circle cx="600" cy="1293" r="185" fill="none" stroke="url(#ring)" stroke-width="3"/>
    <g role="img" aria-label="General health visits icon"><circle cx="478" cy="1155" r="47" fill="#8cc63f"/><circle cx="478" cy="1155" r="22" fill="none" stroke="#fff" stroke-width="2"/></g>
    <g role="img" aria-label="Telemedicine icon"><circle cx="728" cy="1155" r="47" fill="#8cc63f"/><circle cx="728" cy="1155" r="22" fill="none" stroke="#fff" stroke-width="2"/></g>
    <g role="img" aria-label="Physical exams icon"><circle cx="421" cy="1296" r="47" fill="#1a75bd"/><circle cx="421" cy="1296" r="22" fill="none" stroke="#fff" stroke-width="2"/></g>
    <g role="img" aria-label="Medical imaging icon"><circle cx="779" cy="1296" r="47" fill="#1a75bd"/><circle cx="779" cy="1296" r="22" fill="none" stroke="#fff" stroke-width="2"/></g>
    <g role="img" aria-label="Vaccinations icon"><circle cx="494" cy="1435" r="47" fill="#8cc63f"/><circle cx="494" cy="1435" r="22" fill="none" stroke="#fff" stroke-width="2"/></g>
    <g role="img" aria-label="Lab testing icon"><circle cx="726" cy="1435" r="47" fill="#8cc63f"/><circle cx="726" cy="1435" r="22" fill="none" stroke="#fff" stroke-width="2"/></g>
  </svg>
  <div class="brand" style="left:0;width:1200px;text-align:center;top:1276px;font-size:27px;">Valmora Health</div>

  <div class="service right-align abs" style="left:143px;top:1110px;width:260px">
    <h3>GENERAL HEALTH VISITS</h3>
    <p>Sed ut perspiciatis unde omnis iste natus error sit voluptatem</p>
  </div>
  <div class="service abs" style="left:807px;top:1110px">
    <h3>TELEMEDICINE</h3>
    <p>Sed ut perspiciatis unde omnis iste natus error sit voluptatem</p>
  </div>
  <div class="service right-align abs" style="left:89px;top:1255px;width:260px">
    <h3>PHYSICAL EXAMS</h3>
    <p>Sed ut perspiciatis unde omnis iste natus error sit voluptatem</p>
  </div>
  <div class="service abs" style="left:853px;top:1253px">
    <h3>MEDICAL IMAGING</h3>
    <p>Sed ut perspiciatis unde omnis iste natus error sit voluptatem</p>
  </div>
  <div class="service right-align abs" style="left:161px;top:1404px;width:260px">
    <h3>VACCINATIONS</h3>
    <p>Sed ut perspiciatis unde omnis iste natus error sit voluptatem</p>
  </div>
  <div class="service abs" style="left:799px;top:1401px">
    <h3>ADDITIONAL LAB TESTING</h3>
    <p>Sed ut perspiciatis unde omnis iste natus error sit voluptatem</p>
  </div>

  <!-- welcome -->
  <svg class="abs" style="left:0;top:1511px" width="1200" height="714" viewBox="0 0 1200 714">
    <defs>
      <linearGradient id="welcomeFill" x1="0" y1="0" x2="1" y2="0">
        <stop offset="0" stop-color="#2aa6e0"/>
        <stop offset=".5" stop-color="#1e88d0"/>
        <stop offset="1" stop-color="#1a78c2"/>
      </linearGradient>
      <linearGradient id="photoFade" x1="0" y1="0" x2="1" y2="0">
        <stop offset="0" stop-color="#9fd3ef" stop-opacity=".35"/>
        <stop offset="1" stop-color="#9fd3ef" stop-opacity="0"/>
      </linearGradient>
    </defs>
    <path d="M0 0Q600 202 1200 0V631Q600 797 0 631Z" fill="url(#welcomeFill)"/>
    <path role="img" aria-label="Photo of a smiling doctor with a stethoscope beside a colleague" d="M0 0Q330 115 680 95V714Q300 740 0 631Z" fill="url(#photoFade)"/>
  </svg>
  <div class="welcome">
    <div class="kicker">WELCOME TO</div>
    <h2>VALMORA HEALTH</h2>
    <p>Sed ut perspiciatis unde omnis iste natus error sit voluptatem accusantium doloremque laudantium, totam rem aperiam, eaque ipsa quae ab illo inventore veritatis et quasi architecto beatae vitae dicta sunt explicabo.Nemo enim ipsam voluptatem quia voluptas sit aspernatur aut odit aut fugit, sed quia consequuntur magni dolores eos qui ratione voluptatem sequi nesciunt. Neque porro quis ipsum quia dolor sit amet, consectetur</p>
  </div>
  <div class="pill">READ MORE</div>

  <!-- blog -->
  <div class="section-title" style="top:2289px">LATEST BLOG</div>
  <div class="rule" style="top:2347px"></div>

  <div class="card" style="left:112px;top:2401px">
    <svg class="thumb" role="img" aria-label="Photo of a group of smiling doctors in white coats"><rect width="306" height="207" fill="#c7ccd2"/></svg>
    <h3>Nemo enim ipsam voluptat quia voluptas sit enim</h3>
    <div class="date"><svg width="13" height="13" viewBox="0 0 13 13"><rect x=".5" y="1.5" width="12" height="11" fill="none" stroke="#333"/><rect x="0" y="1" width="13" height="3" fill="#333"/></svg>FEB 3, 2021</div>
    <p>Sed ut perspiciatis unde omnis iste nat us error sit voluptatem accusantium dol oremque laudantium, totam</p>
    <span class="btn">READ MORE</span>
  </div>
  <div class="card" style="left:447px;top:2385px">
    <svg class="thumb" role="img" aria-label="Photo of a doctor showing a laptop to an older patient"><rect width="306" height="207" fill="#8d9aa6"/></svg>
    <h3>Nemo enim ipsam voluptat quia voluptas sit enim</h3>
    <div class="date"><svg width="13" height="13" viewBox="0 0 13 13"><rect x=".5" y="1.5" width="12" height="11" fill="none" stroke="#333"/><rect x="0" y="1" width="13" height="3" fill="#333"/></svg>FEB 3, 2021</div>
    <p>Sed ut perspiciatis unde omnis iste nat us error sit voluptatem accusantium dol oremque laudantium, totam</p>
    <span class="btn">READ MORE</span>
  </div>
  <div class="card" style="left:781px;top:2401px">
    <svg class="thumb" role="img" aria-label="Photo of a doctor examining a young girl with her mother"><rect width="306" height="207" fill="#9a8d82"/></svg>
    <h3>Nemo enim ipsam voluptat quia voluptas sit enim</h3>
    <div class="date"><svg width="13" height="13" viewBox="0 0 13 13"><rect x=".5" y="1.5" width="12" height="11" fill="none" stroke="#333"/><rect x="0" y="1" width="13" height="3" fill="#333"/></svg>FEB 3, 2021</div>
    <p>Sed ut perspiciatis unde omnis iste nat us error sit voluptatem accusantium dol oremque laudantium, totam</p>
    <span class="btn">READ MORE</span>
  </div>

  <!-- faq -->
  <div class="faq-bg"></div>
  <div class="section-title" style="top:3009px">OUR FAQ’S</div>
  <div class="rule" style="top:3067px"></div>
  <div class="faq-item" style="top:3113px">Sed ut perspiciatis unde omnis iste natus error sit voluptatem accusantiu?<svg width="23" height="23" viewBox="0 0 23 23"><circle cx="11.5" cy="11.5" r="11.5" fill="#1a75bd"/><path d="M9 6.5l5 5-5 5" fill="none" stroke="#fff" stroke-width="2.6"/></svg></div>
  <div class="faq-item" style="top:3192px">Sed ut perspiciatis unde omnis iste natus error sit voluptatem accusantiu?<svg width="23" height="23" viewBox="0 0 23 23"><circle cx="11.5" cy="11.5" r="11.5" fill="#1a75bd"/><path d="M9 6.5l5 5-5 5" fill="none" stroke="#fff" stroke-width="2.6"/></svg></div>
  <div class="faq-item" style="top:3272px">Sed ut perspiciatis unde omnis iste natus error sit voluptatem accusantiu?<svg width="23" height="23" viewBox="0 0 23 23"><circle cx="11.5" cy="11.5" r="11.5" fill="#1a75bd"/><path d="M9 6.5l5 5-5 5" fill="none" stroke="#fff" stroke-width="2.6"/></svg></div>
  <div class="faq-item" style="top:3351px">Sed ut perspiciatis unde omnis iste natus error sit voluptatem accusantiu?<svg width="23" height="23" viewBox="0 0 23 23"><circle cx="11.5" cy="11.5" r="11.5" fill="#1a75bd"/><path d="M9 6.5l5 5-5 5" fill="none" stroke="#fff" stroke-width="2.6"/></svg></div>

  <!-- footer -->
  <svg class="abs" style="left:0;top:3428px" width="1200" height="423" viewBox="0 0 1200 423">
    <path d="M0 0Q600 154 1200 0V423H0Z" fill="#0b3f95"/>
  </svg>

  <div class="brand" style="left:112px;top:3583px;color:#fff;font-size:33px;">Valmora Health</div>
  <p class="foot-text abs" style="left:112px;top:3655px;width:313px;font-size:13px;text-align:justify">Sed ut perspiciatis unde omnis iste natus error sit voluptatem accusantium dolorque laudantium, totam rem aperiam, eaque ipsa quae ab illo inven-veritatis et quasi architecto beatae</p>

  <div class="foot-head abs" style="left:470px;top:3563px">CONTACT US</div>
  <div class="contact-row" style="top:3618px">
    <svg width="24" height="24" viewBox="0 0 24 24"><path d="M12 2a7 7 0 0 0-7 7c0 5 7 13 7 13s7-8 7-13a7 7 0 0 0-7-7z" fill="none" stroke="#fff" stroke-width="1.5"/><circle cx="12" cy="9" r="2.5" fill="none" stroke="#fff" stroke-width="1.5"/></svg>
    <div>Valmora Health<br>250 ipsam voluptatem<br>quia voluptas</div>
  </div>
  <div class="contact-row" style="top:3703px">
    <svg width="24" height="24" viewBox="0 0 24 24"><path d="M6 3l3 4-2 2c1 3 4 6 7 7l2-2 4 3-2 3C10 20 4 14 3 6z" fill="none" stroke="#fff" stroke-width="1.5"/></svg>
    <div>Phone :<br>000.555.0147</div>
  </div>
  <div class="contact-row" style="top:3774px">
    <svg width="24" height="24" viewBox="0 0 24 24"><rect x="2" y="5" width="20" height="14" fill="none" stroke="#fff" stroke-width="1.5"/><path d="M2 5l10 8 10-8" fill="none" stroke="#fff" stroke-width="1.5"/></svg>
    <div>Email :<br>info@valmorahealth.example</div>
  </div>

  <div class="foot-head abs" style="left:765px;top:3558px">NEWSLETTER</div>
  <p class="foot-text abs" style="left:765px;top:3612px;width:330px">Excepteur sint occaecat cupidatat non proid ent, sunt in culpa qui enim ipsam</p>
  <div class="email-field">Enter Email</div>
  <div class="subscribe">SUBSCRIBE</div>

  <div class="bottom-bar"></div>
  <div class="social" style="left:502px"></div>
  <div class="social" style="left:546px"></div>
  <div class="social" style="left:591px"></div>
  <div class="social" style="left:635px"></div>
  <div class="copyright">Copyright © Valmora Health 2021. All rights reserved.</div>

</div>
</body>
</html>
```